Online Psychiatry business - Business Card

I need a business card design. The target audience is busy professionals of any field (this therapy appeals best to 24-35 year olds). It involves psychiatry by tele-medicine (or video-conference). Nothing on it should be a giveaway that it's about mental health. Professional design with silver or gold as the primary colors appeals to me. The card must be as simple and as uncluttered as possible. Some color and flowing design on the edge of the card appeals to me.
CalmHarborDirect.net should probably appear in the center of the card and stand out, i.e. bold lettering, and easy to read, no cursive, but Ariel Black. Some where below this, should appear "Too Busy to Take Care of Yourself? Think again." Since this isn't office based, I don't think an office address is necessary and limits clutter.
Information that does need to appear is my name: Gerald Mossvane, MD
General phone number: 555-417-8062. I'm hoping to get an 24-hour answering service soon so leave a little room for this. In addition I want to include two email addresses:
CalmHarborDirect@mailbox-example.net and CalmHarbor247@mailbox-example.net
Updates

I like the designs. I would like someone to put the website in bold in the center

 as most have been doing with a smaller font reminder nearby saying "No time" etc.
but I'd like to put my name down in the corner with the rest of the contact material.
Black print against a white or grey background appeals to me, with darker silver artwork near the sides (simple abstract, like wavy lines or something you can one up with that works. 
thanks

I ve tried to provide as much feedback as possible given my time limits, so if you have extra questions, please feel free to email. I tried to attach a file of a business card I really like but make be difficult to actually manufacture. I'm going to send you a link to the photo. The card has a pull tab. There is not much information on the outside. In fact, if you were to design the outside, I would just print : Too Busy to Take Care of Yourself? Think Again.

When you pull the tab the remaining information is on the bottom half of the card. Please don't use the color pink!!!!
http://www.cardgallery-example.org/2009/05/100-clever-print-ideas/
It is the 39th photo on the list, about 2/3ds of the way down the page. It is titled: Faltenkiste

#7 and #16 have an appeal to me, except for the dot patterns
Hope this helps

I'm running out of time and energy. I 've been trying to give do down the list and give  individual feedback but I won't be able to do that anymore.

So if you have any specific questions, write me, and again thank you for all your effort!!

I know i received your files, including your zip files, Pindrel,

but Milo, did you send me the files including ZIP on project 6143907?
thanks

Target Market(s)

Working professionals and executive, attorneys, etc.

Industry/Entity Type

Business

Logo Text

Don't Have Time to Take Care of Yourself? Think Again.

Logo styles of interest
Pictorial/Combination Logo
Wordmark Logo
Font styles to use
Other font styles liked:
• Ariel Black appeals to me the most

Requirements
Must have
• Want to emphasize that the website must be obvious, easily found (The CalmHarborDirect.net)
For that reason i'd like the card to be white, and minimal decoration on one or both sides just to add some style and color
Nice to have
• A Very uncluttered, elegant design, and something that makes it stick in your head-doesn't everyone want the last?
Should not have
• Nothing on the card that give it away that this is about psychiatry, such as brain or other symbol, but also nothing that gives it away as a medical business, such as a stethoscope or red cross or anything.

```html
<!DOCTYPE html>
<html lang="en">
<head>
<meta charset="utf-8">
<title>CalmHarborDirect.net – Business Card</title>
<link rel="stylesheet" href="https://fonts.googleapis.com/css2?family=Arimo:wght@400;700&family=Open+Sans:wght@400;600&display=swap">
<style>
  :root {
    --backdrop: #4a4039;
    --card-white: #ffffff;
    --ink-dark: #333333;
    --ink-grey: #555555;
    --accent-orange: #e0891a;
    --gold-light: #fbf3a6;
    --gold-mid: #e2c46a;
    --gold-deep: #b27c2c;
    --divider: #e3c58a;
  }
  * { margin: 0; padding: 0; box-sizing: border-box; }
  html, body { width: 1200px; height: 418px; overflow: hidden; }
  body { background: var(--backdrop); position: relative; font-family: "Open Sans", Arial, sans-serif; }

  .card {
    position: absolute;
    top: 91px;
    width: 465px;
    height: 264px;
    box-shadow: 3px 4px 8px rgba(0,0,0,0.45);
  }

  /* Front side */
  .card-front { left: 122px; background: var(--card-white); }
  .front-domain {
    position: absolute; top: 46px; width: 100%; text-align: center;
    font-family: "Arimo", Arial, sans-serif; font-weight: 700;
    font-size: 27px; color: var(--ink-dark); letter-spacing: 0.2px;
  }
  .front-tagline {
    position: absolute; top: 83px; width: 100%; text-align: center;
    font-size: 11.5px; font-weight: 600; color: var(--accent-orange);
  }
  .name-band {
    position: absolute; top: 175px; left: 0; width: 100%; height: 26px;
    background: linear-gradient(90deg, var(--gold-light) 0%, var(--gold-mid) 55%, var(--gold-deep) 100%);
    border-top: 1px solid var(--gold-deep);
    border-bottom: 1px solid var(--gold-deep);
    display: flex; align-items: center; justify-content: center;
  }
  .name-band .holder-name {
    font-family: "Arimo", Arial, sans-serif; font-weight: 700;
    font-size: 15.5px; color: var(--ink-dark);
  }
  .contact-phone {
    position: absolute; top: 216px; left: 54px; font-size: 11.5px;
    color: var(--accent-orange); white-space: nowrap;
  }
  .contact-phone .number { color: #111; }
  .contact-note {
    position: absolute; top: 234px; right: 257px; font-size: 9.5px;
    color: var(--accent-orange); white-space: nowrap;
  }
  .contact-divider {
    position: absolute; top: 215px; left: 233px; width: 1px; height: 32px;
    background: var(--divider);
  }
  .contact-emails {
    position: absolute; top: 216px; left: 252px; font-size: 10px;
    line-height: 14px; color: var(--ink-grey); white-space: nowrap;
  }

  /* Back side */
  .card-back {
    left: 629px;
    background: linear-gradient(180deg, var(--gold-light) 0%, var(--gold-mid) 50%, var(--gold-deep) 100%);
  }
  .back-domain {
    position: absolute; top: 125px; width: 100%; text-align: center;
    font-family: "Arimo", Arial, sans-serif; font-weight: 700;
    font-size: 22px; color: #ffffff;
    text-shadow: 1px 1px 2px rgba(0,0,0,0.35);
  }
  .back-tagline {
    position: absolute; top: 163px; width: 100%; text-align: center;
    font-family: "Arimo", Arial, sans-serif; font-weight: 700;
    font-size: 10.5px; color: #111; letter-spacing: 0.3px;
  }
</style>
</head>
<body>
  <section class="card card-front">
    <h1 class="front-domain">CalmHarborDirect.net</h1>
    <p class="front-tagline">Too Busy to Take Care of Yourself? Think again.</p>
    <div class="name-band"><span class="holder-name">Gerald Mossvane, MD</span></div>
    <p class="contact-phone">General Phone: <span class="number">555-417-8062</span></p>
    <p class="contact-note">24-hour answering service</p>
    <div class="contact-divider"></div>
    <p class="contact-emails">CalmHarborDirect@mailbox-example.net<br>CalmHarbor247@mailbox-example.net</p>
  </section>

  <section class="card card-back">
    <h2 class="back-domain">CalmHarborDirect.net</h2>
    <p class="back-tagline">NO TIME TO TAKE CARE OF YOURSELF?</p>
  </section>
</body>
</html>
```